Stationery & Envelope Design

Executive Style looking stationery & envelope design.
Business Information:
TKL Executive Realty
2875 Birchwood Lane, Roseville, CA 95661-4180
Phone: 916.555.0142
Fax: 916.555.0187

Industry/Entity Type

Business

```html
<!DOCTYPE html>
<html lang="en">
<head>
<meta charset="utf-8">
<title>TKL Executive Realty — Letterhead</title>
<link href="https://fonts.googleapis.com/css2?family=Montserrat:wght@500;600&family=Tinos:ital,wght@0,400;1,400&display=swap" rel="stylesheet">
<style>
  :root {
    --backdrop: #e4e4e4;
    --paper: #ffffff;
    --ink: #1b1b1b;
    --accent-blue: #1f4e9c;
    --accent-green: #7a9a2e;
    --muted: #5a6a80;
    --placeholder: #d6d9de;
  }
  * { box-sizing: border-box; margin: 0; padding: 0; }
  html, body {
    width: 1200px; height: 909px; overflow: hidden;
    background: var(--backdrop);
  }
  .letterhead {
    position: absolute;
    left: 280px; top: 28px;
    width: 640px; height: 853px;
    background: var(--paper);
    box-shadow: 0 6px 24px rgba(0,0,0,.12);
    padding: 56px 62px 48px 66px;
    font-family: "Tinos", "Times New Roman", serif;
    color: var(--ink);
  }
  .masthead {
    display: flex; justify-content: space-between; align-items: flex-start;
    margin-bottom: 70px;
  }
  .brand {
    display: flex; align-items: center; gap: 8px;
    margin-top: 52px;
  }
  .brand-mark {
    width: 22px; height: 22px; background: var(--placeholder);
  }
  .brand-name {
    font-family: "Tinos", "Times New Roman", serif;
    font-weight: 400; font-size: 15px;
    color: var(--ink);
  }
  .contact {
    font-style: normal;
    font-family: "Montserrat", Arial, sans-serif;
    font-size: 7.5px; line-height: 1.7;
    color: var(--muted);
    letter-spacing: .08em;
  }
  .contact-company {
    color: var(--accent-blue); font-weight: 600; font-size: 8px;
  }
  .contact-line { display: flex; align-items: center; gap: 5px; }
  .contact-line svg { width: 8px; height: 8px; fill: var(--accent-green); }
  .letter-body { font-size: 12.3px; line-height: 1.36; text-align: justify; }
  .letter-body p { margin-bottom: 14px; }
  .letter-body .salutation { margin-bottom: 12px; }
  .closing { margin-top: 44px; font-size: 12.3px; line-height: 1.35; }
  .signature {
    display: block; width: 92px; height: 30px; margin: 6px 0 2px;
    background: linear-gradient(90deg, rgba(40,40,40,.18), rgba(40,40,40,.08));
    border-radius: 3px;
  }
  .signer { font-size: 11.5px; }
</style>
</head>
<body>
  <article class="letterhead">
    <header class="masthead">
      <div class="brand">
        <span class="brand-mark"></span>
        <span class="brand-name">TKL Executive Realty</span>
      </div>
      <address class="contact">
        <div class="contact-company">TKL Executive Realty</div>
        <div>2875 Birchwood Lane, Roseville, CA 95661-4180</div>
        <div class="contact-line">
          <svg viewBox="0 0 10 10"><path d="M2 1h2l1 2.5-1.2 1a6 6 0 0 0 2.7 2.7l1-1.2L10 7v2a1 1 0 0 1-1 1A9 9 0 0 1 0 2a1 1 0 0 1 1-1z"/></svg>
          916.555.0142
        </div>
        <div class="contact-line">
          <svg viewBox="0 0 10 10"><rect x="1" y="3" width="8" height="5" rx="1"/><rect x="3" y="1" width="4" height="2"/></svg>
          916.555.0187
        </div>
      </address>
    </header>

    <section class="letter-body">
      <p class="salutation">Gentlemen,</p>
      <p>Enclosed I have the honor to send you an article which I should be pleased if you would accept for the “Meridian Review”. I am <em>desperately</em> pushed for money; and in the event of Mr. Hallorand’s liking the “Landscape-Garden” I would take it as an especial favor if you would mail me the amount due for it, so as to reach me here by the 21st, on which day I shall need it. Can you possibly oblige me in this? If you accept the paper I presume you will allow me your usual sum, whatever that is for similar contributions—but I set no price—leaving all to your own liberality. The piece will make 8 of your pages and rather more.</p>
      <p>Will you be kind enough to put the best possible interpretation upon my behavior while in N-York? You must have conceived a <em>queer</em> idea of me—but the simple truth is that Whitcombe would insist upon <em>the juleps</em>, and I knew not what I was either doing or saying. The Review of Darrow, which I offered you was deficient in a 1/2 page of commencement, which I had written to supersede the old beginning, and which gave the article the character of a general and retrospective review. No wonder you did not take it—I would have been very much mortified if you had. I hope to see you at some future time, under better auspices.</p>
    </section>

    <footer class="closing">
      <div>In the meantime I remain</div>
      <div>Yours very truly,</div>
      <span class="signature" role="img" aria-label="Handwritten signature"></span>
      <div class="signer">Edwin Alder Pryce</div>
    </footer>
  </article>
</body>
</html>
```